LM-Steuerberatung WordPress Site fully implemented (tax advisor)

Hello!
I need a little Wordpress Site for my newly founded Tax-Advisor Company.
I am a one-man Office advising in the area of Crypto-Currency.
PLEASE only provide a Design, if you can also Implement a WP-Site afterwards on an existing Webspace.

Please find the Content and Website-Description in the attached Document

Language for the Website is German (for now)

Target Market(s)

Tax-Advisory (specialized in Crypto Currency)

Coding

Coded - Design and coding required

Number of Pages Required

5+ page

Font styles to use
Sans Serif

Requirements
Must have
• Wordpress Implementation afterwards - Details according to attached Project Information Document

```html
<!DOCTYPE html>
<html lang="de">
<head>
<meta charset="utf-8">
<title>LM-Steuerberatung – Kollegendienst</title>
<link rel="stylesheet" href="https://fonts.googleapis.com/css2?family=Poppins:wght@400;500;600;700&display=swap">
<style>
:root{
  --navy:#1c2a45;
  --navy-deep:#0f1a33;
  --ink:#1c2a45;
  --text:#5e5e5e;
  --muted:#8a93a8;
  --grey-line:#b9b9b9;
  --white:#ffffff;
}
*{margin:0;padding:0;box-sizing:border-box}
html,body{width:817px;height:1200px;overflow:hidden}
body{font-family:'Poppins',sans-serif;background:var(--white);position:relative;color:var(--text)}
.topbar{position:absolute;left:0;top:0;width:817px;height:30px;background:var(--navy);color:var(--white);font-size:10.5px}
.topbar .social{position:absolute;left:62px;top:10px;display:flex;gap:14px;align-items:center}
.dot{width:9px;height:9px;border-radius:50%;background:var(--white);display:block}
.sep{width:2px;height:10px;border-left:2px dotted #5a6a88}
.topbar .mail{position:absolute;left:388px;top:8px;display:flex;gap:8px;align-items:center}
.topbar .divider{position:absolute;left:582px;top:7px;width:1px;height:16px;background:#44537a}
.topbar .phone{position:absolute;left:610px;top:8px;display:flex;gap:8px;align-items:center}
.topbar b{font-weight:600}
.header{position:absolute;left:0;top:30px;width:817px;height:52px;background:var(--white);z-index:2}
.logo-tab{position:absolute;left:62px;top:30px;width:203px;height:62px;background:var(--white);clip-path:polygon(0 0,100% 0,100% 80%,94% 100%,7% 100%,0 80%);z-index:2}
.brand{position:absolute;display:flex;align-items:center;gap:7px;font-weight:600;letter-spacing:.3px;z-index:3}
.brand .mark{width:15px;height:15px;border-radius:50%;background:var(--navy)}
.header-brand{left:76px;top:52px;font-size:12.5px;color:var(--ink)}
.nav{position:absolute;top:51px;left:324px;display:flex;gap:24px;font-size:10.5px;color:#6a6a6a;z-index:3}
.nav .active{color:var(--ink);font-weight:500}
.btn-contact{position:absolute;left:646px;top:41px;width:107px;height:31px;border:1.5px solid var(--ink);border-radius:16px;display:flex;align-items:center;justify-content:center;gap:10px;font-size:10px;font-weight:600;color:var(--ink);letter-spacing:.5px;z-index:3}
.hero{position:absolute;left:0;top:82px;width:817px;height:189px;background:linear-gradient(90deg,#1d2a3c 0%,#3a3026 35%,#6a4a2c 60%,#4a3524 85%,#2c2a2a 100%);display:flex;align-items:center;justify-content:center}
.hero h1{color:var(--white);font-size:27px;font-weight:700;letter-spacing:.5px}
.intro{position:absolute;left:0;top:320px;width:817px;text-align:center}
.intro h2{font-size:13.5px;font-weight:600;color:#585858;line-height:21.6px}
.intro p{margin-top:14px;font-size:11.6px;line-height:21.6px;color:#666}
.arrow{position:absolute;left:386px;top:490px}
.photo-frame{position:absolute;left:113px;top:578px;width:625px;height:223px;border-right:3px solid var(--grey-line);border-bottom:3px solid var(--grey-line);border-bottom-right-radius:14px}
.photo{position:absolute;left:87px;top:552px;width:643px;height:242px;border-radius:18px;background:linear-gradient(90deg,#3b3632 0%,#7a6a5c 40%,#a69a8c 60%,#4d4844 80%,#8e8c86 100%)}
.cta{position:absolute;left:269px;top:838px;width:279px;height:37px;border-radius:19px;background:var(--navy);color:var(--white);font-size:10px;font-weight:700;display:flex;align-items:center;justify-content:center;gap:10px;letter-spacing:.2px}
.cta .dot{width:10px;height:10px}
.footer{position:absolute;left:0;top:933px;width:817px;height:267px;background:linear-gradient(160deg,#0e1a36,#12203f 60%,#0c1630);color:var(--white)}
.footer-brand{left:63px;top:82px;font-size:12.5px;color:var(--white)}
.footer-brand .mark{background:var(--white)}
.footer .about{position:absolute;left:63px;top:104px;width:250px;font-size:11.5px;line-height:21.6px;color:var(--muted)}
.footer .copy{position:absolute;left:63px;top:188px;font-size:10.5px;color:var(--muted)}
.footer h3{position:absolute;top:56px;font-size:13px;font-weight:600;letter-spacing:.3px}
.links{position:absolute;left:395px;top:85px;list-style:none;font-size:11.5px;color:var(--muted)}
.links li{height:25.7px;display:flex;align-items:center;gap:8px}
.info{position:absolute;left:577px;display:flex;gap:15px;align-items:center}
.info .box{width:34px;height:29px;background:#e1e3e8;border-radius:4px;display:flex;align-items:center;justify-content:center}
.info .label{font-size:11px;color:var(--muted);line-height:16px}
.info .val{font-size:11.5px;color:var(--white);line-height:17px}
.footer .social-row{position:absolute;left:577px;top:191px;display:flex;align-items:center;gap:22px;font-size:11.5px;color:var(--muted)}
</style>
</head>
<body>
<div class="topbar">
  <div class="social"><span class="dot"></span><span class="sep"></span><span class="dot"></span><span class="sep"></span><span class="dot"></span></div>
  <div class="mail"><svg width="14" height="12" viewBox="0 0 14 12"><rect x="1" y="1" width="12" height="10" rx="1.5" fill="none" stroke="#fff" stroke-width="1.2"/><path d="M1.5 2 7 7l5.5-5" fill="none" stroke="#fff" stroke-width="1.2"/></svg>Email: office@lm-steuer.example</div>
  <div class="divider"></div>
  <div class="phone"><svg width="13" height="13" viewBox="0 0 13 13"><path d="M2.5 1.5 4.5 1l1.2 2.8-1.3 1a7 7 0 0 0 3.6 3.6l1-1.3L12 8.3l-.5 2A1.5 1.5 0 0 1 10 11.6C5.5 11.3 1.7 7.5 1.4 3a1.5 1.5 0 0 1 1.1-1.5z" fill="none" stroke="#fff" stroke-width="1.1"/></svg>Phone: <b>+43 512 000 111</b></div>
</div>
<div class="header"></div>
<div class="logo-tab"></div>
<div class="brand header-brand"><span class="mark"></span>LM STEUERBERATUNG</div>
<nav class="nav"><span>HOME</span><span class="active">LEISTUNGEN ▾</span><span>ÜBER MICH</span><span>IMPRESSUM</span></nav>
<div class="btn-contact">KONTAKT <svg width="14" height="14" viewBox="0 0 14 14"><circle cx="7" cy="7" r="6" fill="none" stroke="#1c2a45" stroke-width="1.1"/><path d="M3.5 7h6M7 4.5 9.5 7 7 9.5" fill="none" stroke="#1c2a45" stroke-width="1.1"/></svg></div>

<section class="hero" role="img" aria-label="Hintergrundfoto: Geschäftsleute legen am Holztisch die Hände zusammen"><h1>KOLLEGENDIENST</h1></section>

<section class="intro">
  <h2>Ihr Fokus liegt in der traditionellen Steuerberatung und Sie haben keine Zeit sich<br>das hochkomplexe Spezialthema Kryptowährungen etc. einzuarbeiten?</h2>
  <p>Um Ihre Klienten dennoch weiterhin vollumfänglich beraten zu können, biete ich Ihnen<br>gerne mein Know-How und die gesamte Leistungspalette an um Ihre Kunden ganz<br>nach Ihrem Wunsch entweder direkt oder diskret im Hintergrund bei sämtlichen<br>Themen rund um Krypto mit steuerlicher Expertise dazu zu unterstützen.</p>
</section>

<svg class="arrow" width="46" height="40" viewBox="0 0 46 40"><path d="M43 3C28 3 18 14 11 36" fill="none" stroke="#1c2a45" stroke-width="2" stroke-linecap="round"/><path d="M3 27l8 9 7-9" fill="none" stroke="#1c2a45" stroke-width="2" stroke-linecap="round" stroke-linejoin="round"/></svg>

<div class="photo-frame"></div>
<div class="photo" role="img" aria-label="Foto: vier Kolleginnen und Kollegen in Businesskleidung besprechen gemeinsam Unterlagen"></div>

<div class="cta">NEHMEN SIE GERNE KONTAKT MIT MIR AUF! <span class="dot"></span></div>

<footer class="footer">
  <div class="brand footer-brand"><span class="mark"></span>LM STEUERBERATUNG</div>
  <p class="about">Ihrem Spezialisten bei allen steuerlichen Themen rund um Einkünfte &amp; Vermögen aus Krypto-Assets.</p>
  <p class="copy">Copyright © 2022 LM-Steuerberatung</p>
  <h3 style="left:395px">QUICK LINKS</h3>
  <ul class="links">
    <li>›<span>Home</span></li><li>›<span>Leistungen</span></li><li>›<span>Über mich</span></li><li>›<span>Impressum</span></li><li>›<span>Kontakt</span></li>
  </ul>
  <h3 style="left:577px">CONTACT INFORMATION</h3>
  <div class="info" style="top:90px"><div class="box"><svg width="12" height="10" viewBox="0 0 12 10"><rect x="1" y="1" width="10" height="8" rx="1" fill="#fff"/></svg></div><div><div class="label">Email:</div><div class="val">office@lm-steuer.example</div></div></div>
  <div class="info" style="top:138px"><div class="box"><svg width="12" height="12" viewBox="0 0 13 13"><path d="M2.5 1.5 4.5 1l1.2 2.8-1.3 1a7 7 0 0 0 3.6 3.6l1-1.3L12 8.3l-.5 2A1.5 1.5 0 0 1 10 11.6C5.5 11.3 1.7 7.5 1.4 3a1.5 1.5 0 0 1 1.1-1.5z" fill="#fff"/></svg></div><div><div class="label">Phone:</div><div class="val">+43 512 000 111</div></div></div>
  <div class="social-row">Social Media: <span class="dot"></span><span class="dot"></span><span class="dot"></span></div>
</footer>
</body>
</html>
```